Redesign website for small print company

Vindurgata is a small printing company in Iceland mainly servicing Students, schools, etc. We are also doing all kind of other jobs, like business cards, book printing, brochure printing etc. We are also selling books online.
Our website is: www.vindurgata.is
What we are looking for is:
- Web Design (Uncoded - PSD layout only)
- Mobile friendly design, using our current color scheme: Red, green, yellow and light gray.
- Clean simple design
- Simple, light and easy to use.
- More menu Items/drop down
Industry/Entity Type
Digital Printing
Number of Pages Required
5+ page
Requirements
Must have
- Easy navigation
- Designed for mobile
- Current color scheme (see logo)
Nice to have
- Icon based products

```html
<!DOCTYPE html>
<html lang="is">
<head>
<meta charset="utf-8">
<title>Vindurgata – Prentþjónusta</title>
<link href="https://fonts.googleapis.com/css2?family=Montserrat:wght@500;600;700;800&family=Open+Sans:wght@400;600&display=swap" rel="stylesheet">
<style>
:root{
  --red:#e3262b;
  --green:#1c8a3c;
  --yellow:#fdd20a;
  --orange:#f29a1f;
  --gray-bg:#f2f3f6;
  --gray-line:#e2e4e8;
  --text:#2b2b2b;
  --muted:#6d6f73;
  --footer:#2a2a2a;
  --white:#fff;
}
*{margin:0;padding:0;box-sizing:border-box}
html,body{width:1200px;height:2392px;overflow:hidden}
body{position:relative;background:var(--white);font-family:"Open Sans",sans-serif;color:var(--text)}
.heading{font-family:"Montserrat",sans-serif}

/* header */
.topbar{position:absolute;top:0;left:0;width:1200px;height:34px;display:flex;justify-content:flex-end;align-items:center;gap:22px;padding-right:92px;font-size:12px;color:var(--muted)}
.topbar b{color:var(--red);font-weight:600;font-size:14px}
.topbar .mail{color:var(--green)}
.header{position:absolute;top:34px;left:0;width:1200px;height:66px;display:flex;align-items:center;padding:0 88px;border-bottom:1px solid var(--gray-line)}
.brand{display:flex;align-items:center;gap:10px;font-family:"Montserrat",sans-serif;font-weight:800;font-size:24px;color:var(--text);letter-spacing:.5px}
.brand-square{width:28px;height:28px;background:var(--red)}
.nav{margin-left:auto;display:flex;gap:38px;font-family:"Montserrat",sans-serif;font-weight:600;font-size:12.5px;letter-spacing:.5px}
.nav a{color:var(--text);text-decoration:none}
.header-icons{display:flex;gap:22px;margin-left:40px}

/* hero */
.hero{position:absolute;top:100px;left:0;width:1200px;height:560px;background:linear-gradient(120deg,#f4f5f7 0%,#e9ecef 40%,#c9cfd8 70%,#b5bcc6 100%)}
.quick{position:absolute;left:78px;width:132px;height:132px;border-radius:50%;display:flex;flex-direction:column;align-items:center;justify-content:center;gap:10px;font-family:"Montserrat",sans-serif;font-weight:700;font-size:10px;letter-spacing:.5px;text-transform:uppercase;box-shadow:0 6px 16px rgba(0,0,0,.15)}
.quick.order{top:120px;background:var(--yellow);color:var(--text)}
.quick.upload{top:280px;background:var(--red);color:var(--white)}
.quick.quote{top:430px;background:var(--green);color:var(--white)}

/* products */
.section-title{position:absolute;left:88px;top:686px;font-weight:800;font-size:22px;letter-spacing:1px}
.title-bar{position:absolute;left:290px;top:700px;width:60px;height:3px;background:linear-gradient(90deg,var(--red) 50%,var(--yellow) 50%)}
.product-grid{position:absolute;left:88px;top:738px;width:1024px;display:grid;grid-template-columns:repeat(3,1fr);gap:14px}
.product{height:268px;background:var(--gray-bg);display:flex;flex-direction:column;align-items:center;justify-content:center;gap:26px;font-family:"Montserrat",sans-serif;font-weight:500;font-size:24px}
.product-icon{height:86px;display:flex;align-items:center;justify-content:center}

/* welcome */
.welcome{position:absolute;top:1350px;left:88px;width:1024px;display:flex;gap:50px}
.welcome-name{width:212px;flex:none;padding-top:8px;font-family:"Montserrat",sans-serif;font-weight:800;font-size:28px;color:var(--red);letter-spacing:.5px}
.welcome h2{font-weight:800;font-size:21px;margin:10px 0 22px}
.welcome p{font-size:13.5px;line-height:1.75;color:var(--muted);margin-bottom:20px}

/* map */
.map{position:absolute;top:1728px;left:0;width:1200px;height:540px;background:linear-gradient(135deg,#eef0ec 0%,#e4e8e1 45%,#cfdde7 75%,#b9d1e3 100%)}
.contact-card{position:absolute;top:1860px;left:88px;width:352px;height:360px;background:var(--white);box-shadow:0 8px 24px rgba(0,0,0,.15);padding:30px 34px}
.contact-card .brand{font-size:18px;margin-bottom:24px}
.contact-card .brand-square{width:20px;height:20px}
.contact-card p{font-size:13px;line-height:1.7;color:var(--muted)}
.socials{display:flex;gap:10px;margin-top:22px}
.socials span{width:26px;height:26px;border-radius:50%}

/* footer */
.footer{position:absolute;top:2272px;left:0;width:1200px;height:120px;background:var(--footer);color:#bbb;padding:26px 88px;font-size:13px}
.footer-links{display:flex;gap:26px;color:#ddd}
.copyright{margin-top:18px;font-size:12px;color:#888}
.cards{position:absolute;right:92px;top:34px;display:flex;gap:12px}
.cards span{width:50px;height:32px;border:1px solid #666;border-radius:4px}
</style>
</head>
<body>

<div class="topbar">
  <span>Call <b>555 0142</b></span>
  <span class="mail">info@vindurgata.is</span>
  <span>Mán - Fös 9-17</span>
  <span>English ▾</span>
</div>

<header class="header">
  <div class="brand"><span class="brand-square"></span>Vindurgata</div>
  <nav class="nav"><a>HOME</a><a>SERVICES</a><a>BOOKS</a><a>JOB SUBMIT</a><a>ABOUT US</a></nav>
  <div class="header-icons">
    <svg width="20" height="20" viewBox="0 0 20 20" fill="none" stroke="#2b2b2b" stroke-width="2.2"><circle cx="8" cy="8" r="6"/><path d="M13 13l5 5"/></svg>
    <svg width="22" height="20" viewBox="0 0 22 20" fill="none" stroke="#2b2b2b" stroke-width="2"><path d="M1 2h4l3 11h11l2-8H6"/><circle cx="9" cy="17" r="1.6"/><circle cx="18" cy="17" r="1.6"/></svg>
  </div>
</header>

<section class="hero" role="img" aria-label="Photograph of smiling students holding books and folders">
  <a class="quick order">
    <svg width="36" height="36" viewBox="0 0 36 36" fill="none" stroke="#2b2b2b" stroke-width="2.4"><path d="M4 6h5l4 16h16l3-12H11"/><circle cx="15" cy="29" r="2.4"/><circle cx="27" cy="29" r="2.4"/></svg>
    Panta núna
  </a>
  <a class="quick upload">
    <svg width="36" height="36" viewBox="0 0 36 36" fill="none" stroke="#fff" stroke-width="2.4"><path d="M18 24V6M11 13l7-7 7 7M6 24v6h24v-6"/></svg>
    Sækja skrá
  </a>
  <a class="quick quote">
    <svg width="36" height="36" viewBox="0 0 36 36" fill="none" stroke="#fff" stroke-width="2.4"><circle cx="18" cy="18" r="12"/><path d="M13 18l4 4 7-8"/></svg>
    Fá tilboð
  </a>
</section>

<h2 class="section-title heading">PRODUCT LIST</h2>
<div class="title-bar"></div>

<div class="product-grid">
  <div class="product">
    <div class="product-icon"><svg width="70" height="80" viewBox="0 0 70 80" fill="none" stroke="#e3262b" stroke-width="3"><path d="M8 4h38l16 16v56H8z"/><path d="M46 4v16h16M20 36h30M20 48h30M20 60h20"/></svg></div>
    Essays
  </div>
  <div class="product">
    <div class="product-icon"><svg width="92" height="62" viewBox="0 0 92 62" fill="none" stroke="#1c8a3c" stroke-width="3"><rect x="3" y="3" width="86" height="56" rx="4"/><circle cx="26" cy="24" r="8"/><path d="M14 44c2-8 22-8 24 0M50 20h28M50 32h28M50 44h18"/></svg></div>
    Business Cards
  </div>
  <div class="product">
    <div class="product-icon"><svg width="78" height="80" viewBox="0 0 78 80" fill="none" stroke="#f29a1f" stroke-width="3"><path d="M6 10l40-6 10 66-40 6z"/><path d="M24 14l40-6 10 62-18 3"/><path d="M16 30l26-4M18 44l26-4M20 58l18-3"/></svg></div>
    Leaflets
  </div>
  <div class="product">
    <div class="product-icon"><svg width="92" height="72" viewBox="0 0 92 72" fill="none" stroke="#1c8a3c" stroke-width="3"><path d="M46 12C36 4 16 4 4 8v58c12-4 32-4 42 4 10-8 30-8 42-4V8C76 4 56 4 46 12z"/><path d="M46 12v58M14 22h22M14 34h22M14 46h22M56 22h22M56 34h22M56 46h22"/></svg></div>
    Book Printing
  </div>
  <div class="product">
    <div class="product-icon"><svg width="84" height="84" viewBox="0 0 84 84" fill="none" stroke="#f29a1f" stroke-width="3"><rect x="6" y="6" width="72" height="50" rx="2"/><path d="M20 44l14-16 12 12 8-8 12 12M42 56v22M28 78h28"/><circle cx="58" cy="20" r="5"/></svg></div>
    Posters
  </div>
  <div class="product">
    <div class="product-icon"><svg width="84" height="80" viewBox="0 0 84 80" fill="none" stroke="#e3262b" stroke-width="3"><path d="M42 6L4 22l38 16 38-16z"/><path d="M18 28v16c0 8 48 8 48 0V28M80 22v18"/><rect x="14" y="54" width="56" height="20" rx="2"/><path d="M24 64h36"/></svg></div>
    Textbooks
  </div>
</div>

<section class="welcome">
  <div class="welcome-name">Vindurgata</div>
  <div>
    <h2 class="heading">VELKOMIN Í VINDURGATA</h2>
    <p>Vindurgata er lítil prentsmiðja sem þjónar nemendum, skólum og fyrirtækjum um allt land. Við leggjum áherslu á vandaða vinnu, sanngjarnt verð og skjóta afgreiðslu.</p>
    <p>Við prentum ritgerðir, lokaverkefni, nafnspjöld, bæklinga, veggspjöld og bækur í litlu og stóru upplagi. Hægt er að senda inn verk á netinu og sækja þau tilbúin til okkar.</p>
    <p>Einnig seljum við kennslubækur og námsgögn í vefverslun okkar með heimsendingu um allt land.</p>
    <p>Vindurgata er staðsett í miðbæ Reykjavíkur, opið alla virka daga.</p>
  </div>
</section>

<div class="map" role="img" aria-label="Street map of central Reykjavík showing the shop location"></div>

<aside class="contact-card">
  <div class="brand"><span class="brand-square"></span>Vindurgata</div>
  <p>Vindurgata ehf. Kt. 000000-0000</p>
  <p>Brekkustígur 4</p>
  <p>101 Reykjavík</p>
  <p>Sími 555 0142</p>
  <p>info@vindurgata.is</p>
  <p>www.vindurgata.is</p>
  <div class="socials">
    <span style="background:var(--yellow)"></span>
    <span style="background:var(--orange)"></span>
    <span style="background:var(--red)"></span>
    <span style="background:var(--red)"></span>
  </div>
</aside>

<footer class="footer">
  <div class="footer-links"><span>Home</span><span>Services</span><span>Skilmálar</span><span>Hafa samband</span></div>
  <div class="copyright">© 2024 Vindurgata</div>
  <div class="cards"><span></span><span></span></div>
</footer>

</body>
</html>
```